New Business card design to reflect rebrand

I would like a business card design with a good base colour for our new logo and also a placeholder for a profile pic of the card holder. the design needs to be editable to the point that we can easily change the picture of the person and use that design for printmerlo etc. we are looking at a metalic finish business card so will need a good base colour to bring out the finish.

Target Market(s)

prospective customers

Industry/Entity Type

Business

Contact Information for Business Card

I would like one editable design that we can change the name of the card holder and profile picture. The design need to be in a format that be send to printmerlo etc.

Our address is Fenwick Lodge, Copse Lane, Elmstead Green, GU14 3TP Tel no. 01483 556172

Requirements
Must have
• place holder for a profile pic for the card holder. in AI or preferably PSD format

```html
<!DOCTYPE html>
<html lang="en">
<head>
<meta charset="utf-8">
<title>Brantwell Workplace Services – Business Card</title>
<link rel="stylesheet" href="https://fonts.googleapis.com/css2?family=Open+Sans:wght@400;600;700&display=swap">
<style>
  :root {
    --slate: #41556f;
    --orange: #e8601c;
    --white: #ffffff;
    --backdrop: #eceef1;
    --photo-top: #c9ccd2;
    --photo-bottom: #2a3142;
  }
  * { box-sizing: border-box; margin: 0; padding: 0; }
  html, body { width: 1200px; height: 900px; overflow: hidden; }
  body {
    position: relative;
    background: var(--backdrop);
    font-family: "Open Sans", Arial, sans-serif;
  }
  .card {
    position: absolute;
    background: var(--white);
    overflow: hidden;
    box-shadow: 0 6px 18px rgba(0,0,0,.18);
  }
  /* front */
  .card-front { left: 78px; top: 35px; width: 588px; height: 363px; }
  .brand { position: absolute; left: 32px; top: 84px; }
  .brand-name {
    font-weight: 700; font-size: 38px; letter-spacing: 1.5px;
    color: var(--slate); line-height: 1;
  }
  .brand-tagline {
    margin-top: 6px; font-size: 16px; letter-spacing: 2.6px;
    color: var(--orange); line-height: 1;
  }
  .info-band {
    position: absolute; left: 0; top: 166px; width: 420px; height: 197px;
    background: var(--slate);
  }
  .holder-name {
    position: absolute; left: 31px; top: 26px;
    color: var(--white); font-weight: 700; font-size: 20px; line-height: 28px;
  }
  .contact { position: absolute; left: 31px; top: 66px; color: var(--white); font-size: 15px; }
  .contact-line { display: flex; align-items: center; gap: 8px; height: 25px; }
  .contact-line svg { width: 11px; height: 11px; flex: none; }
  .address { margin-top: 10px; line-height: 22px; }
  .profile-photo {
    position: absolute; left: 326px; top: 0; width: 262px; height: 363px;
    background: linear-gradient(180deg, var(--photo-top) 0%, #8a8f9c 40%, var(--photo-bottom) 100%);
    clip-path: polygon(32% 0, 100% 0, 100% 100%, 0 100%, 6% 62%, 18% 50%, 26% 47%, 30% 30%, 28% 14%);
    border-left: 4px solid var(--white);
  }
  /* back */
  .card-back { left: 388px; top: 505px; width: 567px; height: 352px; }
  .back-band {
    position: absolute; left: 0; top: 110px; width: 100%; height: 131px;
    background: var(--slate);
    display: flex; flex-direction: column; align-items: center; justify-content: center;
  }
  .back-name {
    color: var(--white); font-weight: 700; font-size: 40px; letter-spacing: 2px; line-height: 1;
  }
  .back-tagline {
    margin-top: 8px; color: var(--white); font-size: 18px; letter-spacing: 3.4px; line-height: 1;
  }
</style>
</head>
<body>
  <section class="card card-front">
    <div class="brand">
      <div class="brand-name">BRANTWELL</div>
      <div class="brand-tagline">WORKPLACE SERVICES</div>
    </div>
    <div class="info-band">
      <div class="holder-name">Daniel Hart</div>
      <div class="contact">
        <div class="contact-line">
          <svg viewBox="0 0 24 24"><path fill="#ffffff" d="M6.6 10.8a15.1 15.1 0 0 0 6.6 6.6l2.2-2.2c.3-.3.7-.4 1-.2 1.1.4 2.3.6 3.6.6.6 0 1 .4 1 1V20c0 .6-.4 1-1 1C10.6 21 3 13.4 3 4c0-.6.4-1 1-1h3.5c.6 0 1 .4 1 1 0 1.3.2 2.5.6 3.6.1.3 0 .7-.2 1z"/></svg>
          <span>01483 556172</span>
        </div>
        <div class="contact-line">
          <svg viewBox="0 0 24 24"><rect x="1" y="4" width="22" height="16" fill="#ffffff"/><polyline points="2,5 12,13 22,5" fill="none" stroke="#41556f" stroke-width="2.5"/></svg>
          <span>info@brantwell.com</span>
        </div>
        <div class="address">Fenwick Lodge, Copse Lane,<br>Elmstead Green, GU14 3TP</div>
      </div>
    </div>
    <div class="profile-photo" role="img" aria-label="Profile photo of the card holder"></div>
  </section>

  <section class="card card-back">
    <div class="back-band">
      <div class="back-name">BRANTWELL</div>
      <div class="back-tagline">WORKPLACE SERVICES</div>
    </div>
  </section>
</body>
</html>
```